Digital One Pager for Consulting Practice

I would like the essence of the content in my ppt consolidated into a one-pager. The one-pager will mainly be sent via email as a pdf and intended to excite and invite new clients and establish the credibility of my boutique high-end consulting firm. Infographics and symbols would be a plus. The target client should view the firm as providing premeir service. The client is getting a thought partner.

Target Market(s)

Large Medical Device Manufacturer Executives, Early-Stage Medical Device Manufacturer Executives, Partners at VC Firms

Industry/Entity Type

Medical Equipment

Colors
0355a3
f37122

Requirements
Must have
• Please match the color scheme in ppt. Please use the existing logo. I am very open to better graphics on the process. My photo does not need to be on the digital flyer. Hyper link to the website and email is needed.
Nice to have
• Infographics

```html
<!DOCTYPE html>
<html lang="en">
<head>
<meta charset="utf-8">
<title>Harlow Ventures — One Pager</title>
<link href="https://fonts.googleapis.com/css2?family=Open+Sans:ital,wght@0,400;0,600;0,700;0,800;1,700;1,800&display=swap" rel="stylesheet">
<style>
  :root{
    --blue:#0355a3;
    --orange:#f37122;
    --navy:#0b1c36;
    --ink:#2b2b2b;
    --grey-band:#e7e8ea;
    --panel:#f3f3f3;
    --badge-border:#a9abae;
  }
  *{margin:0;padding:0;box-sizing:border-box}
  html,body{width:927px;height:1200px;overflow:hidden;background:#fff}
  body{font-family:"Open Sans",sans-serif;color:var(--ink);position:relative}
  .page{position:relative;width:927px;height:1200px;overflow:hidden}
  .abs{position:absolute}

  .band{position:absolute;left:0;top:0;width:927px;height:1200px}

  .brand{left:36px;top:40px;display:flex;align-items:center;gap:14px}
  .brand-dot{width:46px;height:46px;border-radius:50%;background:var(--orange)}
  .brand-name{font-weight:800;font-size:40px;line-height:1;letter-spacing:4px;color:var(--navy)}

  .pillars{left:578px;top:0;width:312px;height:130px;background:var(--navy);border-radius:0 0 0 100px;padding:20px 0 0 56px}
  .pillars li{list-style:none;color:#fff;font-weight:800;font-style:italic;font-size:18px;line-height:23.5px}
  .pillars li::before{content:"• "}

  .heading{color:var(--blue);font-weight:700;font-size:27px;line-height:1.1}
  .body{font-size:13px;line-height:17.5px;color:var(--ink)}
  .body p{margin-bottom:17px}
  .body .tight{margin-bottom:0}
  .body .indent{padding-left:13px}

  .diff-bar{position:absolute;left:216px;height:38px;color:#fff;font-weight:700;font-size:17px;display:flex;align-items:center;gap:8px;padding-left:8px}
  .diff-bar svg{width:18px;height:18px}

  .process{left:480px;top:540px;width:124px}
  .step{position:absolute;left:0;width:124px;color:#fff;font-size:13px;line-height:17px;text-align:center}
  .step svg{display:block;margin:0 auto 6px}

  .badge{position:absolute;width:112px;height:53px;border:2px solid var(--badge-border);background:#fff}
  .badge.navy{background:var(--navy)}
  .badge.blue{background:var(--blue)}

  .service{position:absolute;display:flex;gap:8px}
  .service-icon{width:54px;height:54px;border:4px solid var(--orange);border-radius:50%;display:flex;align-items:center;justify-content:center;flex:none;margin-top:4px}
  .service h3{color:var(--orange);font-weight:700;font-size:13.5px;line-height:14px;margin-bottom:8px}
  .service p{font-size:8.5px;line-height:13px;color:#222}

  .value{left:636px;top:1050px;width:291px;height:150px;background:var(--panel);padding:26px 0 0 42px}
  .value h2{font-size:18px;font-weight:700;color:var(--navy);margin-bottom:16px}
  .contact{display:flex;align-items:center;gap:6px;font-size:8.5px;color:#333;margin-bottom:8px;padding-left:7px}
  .contact a{color:#333;text-decoration:none}
</style>
</head>
<body>
<div class="page">

  <svg class="band" viewBox="0 0 927 1200" aria-hidden="true">
    <path d="M760 170 V820 Q760 980 600 980 H0" fill="none" stroke="var(--grey-band)" stroke-width="36"/>
  </svg>

  <div class="abs brand">
    <span class="brand-dot"></span>
    <span class="brand-name">HARLOW VENTURES</span>
  </div>

  <ul class="abs pillars">
    <li>Extensive Experience</li>
    <li>Efficient Process</li>
    <li>Valued Network</li>
  </ul>

  <h2 class="abs heading" style="left:68px;top:188px;letter-spacing:1.5px">Experience</h2>
  <div class="abs body" style="left:37px;top:248px;width:370px">
    <p>•&nbsp; Over a decade &nbsp;@FDA (Former Deputy Division Director)</p>
    <p>•&nbsp; Expertise: Cardiovascular, Ophthalmology, General Hospital,<br>Infection Control, Dental, Anesthesia, Respiratory</p>
    <p>•&nbsp; Vice President Regulatory Affairs / Quality Assurance @Corvane<br>(Fortune 150 Company)</p>
    <p class="tight">•&nbsp; Initiated &nbsp;reorganization of department</p>
    <p class="tight">•&nbsp; Led major compliance effort</p>
    <p class="tight">•&nbsp; Successful FDA inspection (no observations)</p>
  </div>

  <h2 class="abs heading" style="left:502px;top:150px">Experience to Provide</h2>
  <div class="abs body" style="left:470px;top:211px;width:400px">
    <p>Executive Application Review</p>
    <p class="tight indent">•Examples include: Presubmission, IDE, 510(k) , 513(g), PMA,</p>
    <p class="tight">Refuse to Accept, Hold letter</p>
    <p class="indent">•Troubleshooting</p>
    <p>Strategic Advice &amp; Diligence to Investors</p>
    <p class="tight indent">•Validate &amp; Verify Founder Milestones</p>
    <p class="tight indent">•Diligence portfolio company Regulatory and Quality systems</p>
  </div>

  <h2 class="abs heading" style="left:68px;top:533px">Differentiators</h2>
  <svg class="abs" style="left:37px;top:575px" width="176" height="176" viewBox="0 0 176 176" aria-hidden="true">
    <circle cx="88" cy="88" r="66" fill="none" stroke="#104a94" stroke-width="40"/>
    <path d="M22 88 A66 66 0 0 1 150 64" fill="none" stroke="var(--orange)" stroke-width="40"/>
    <circle cx="88" cy="88" r="46" fill="none" stroke="#ffffff" stroke-opacity=".15" stroke-width="6"/>
  </svg>
  <div class="diff-bar" style="top:596px;width:218px;background:var(--orange)">
    <svg viewBox="0 0 18 18"><circle cx="7" cy="7" r="5" fill="none" stroke="#fff" stroke-width="2.4"/><path d="M11 11l5 5" stroke="#fff" stroke-width="2.6"/></svg>EXPERIENCE</div>
  <div class="diff-bar" style="top:636px;width:164px;background:var(--blue)">
    <svg viewBox="0 0 18 18"><circle cx="9" cy="9" r="2.5" fill="#fff"/><g stroke="#fff" stroke-width="1.4"><path d="M9 9L3 4M9 9l6-5M9 9l-6 5M9 9l6 5"/></g><g fill="#fff"><circle cx="3" cy="4" r="1.6"/><circle cx="15" cy="4" r="1.6"/><circle cx="3" cy="14" r="1.6"/><circle cx="15" cy="14" r="1.6"/></g></svg>NETWORK</div>
  <div class="diff-bar" style="top:674px;width:190px;background:var(--navy)">
    <svg viewBox="0 0 18 18" fill="none" stroke="#fff" stroke-width="2"><path d="M3 8a6 6 0 0 1 11-3M15 10a6 6 0 0 1-11 3"/><path d="M14 1v4h-4M4 17v-4h4"/></svg>PROCESS</div>

  <h2 class="abs heading" style="left:502px;top:464px">Efficient<br>Process</h2>
  <svg class="abs" style="left:480px;top:540px" width="124" height="545" viewBox="0 0 124 545" aria-hidden="true">
    <rect x="0" y="0" width="124" height="497" fill="var(--navy)"/>
    <g fill="var(--orange)">
      <path d="M0 124 H124 L62 164 Z"/>
      <path d="M0 249 H124 L62 289 Z"/>
      <path d="M0 372 H124 L62 412 Z"/>
      <path d="M0 497 H124 L62 541 Z"/>
    </g>
  </svg>
  <div class="process abs">
    <div class="step" style="top:34px">
      <svg width="56" height="56" viewBox="0 0 56 56"><path d="M28 2a26 26 0 1 1-14 48L4 54l4-10A26 26 0 0 1 28 2z" fill="#fff"/><path d="M20 16c-3 2-2 8 3 14s11 9 14 7l2-3-5-4-3 2c-2-1-5-4-6-6l2-3-4-5z" fill="var(--navy)"/><path d="M32 15a9 9 0 0 1 8 8M31 20a4 4 0 0 1 4 4" stroke="var(--navy)" stroke-width="2" fill="none"/></svg>
      Exploratory Call</div>
    <div class="step" style="top:168px">
      <svg width="40" height="40" viewBox="0 0 40 40"><rect x="2" y="2" width="36" height="36" fill="none" stroke="#fff" stroke-width="3"/><path d="M38 2L2 38" stroke="#fff" stroke-width="2"/><path d="M10 11h9M14.5 6.5v9M22 29h9" stroke="#fff" stroke-width="3"/></svg>
      Regulatory<br>Landscape</div>
    <div class="step" style="top:292px">
      <svg width="42" height="40" viewBox="0 0 42 40"><path d="M18 8c9 0 16 6 16 13s-7 13-16 13c-3 0-5 0-7-1l-8 4 3-7C3 27 2 24 2 21 2 14 9 8 18 8z" fill="#fff"/><path d="M33 1l8 13H25z" fill="#fff" stroke="var(--navy)" stroke-width="1.5"/><path d="M33 5v5M33 11.5v1" stroke="var(--navy)" stroke-width="1.6"/></svg>
      Problem<br>Statement</div>
    <div class="step" style="top:414px">
      <svg width="38" height="38" viewBox="0 0 38 38"><path d="M2 2h34v26H12l-8 8v-8H2z" fill="#fff"/><path d="M12 21l14-14 3 3-14 14h-3z" fill="var(--navy)"/><path d="M11 24h17" stroke="var(--navy)" stroke-width="2"/></svg>
      Review &amp; Align<br>on Deliverables</div>
  </div>

  <h2 class="abs heading" style="left:678px;top:522px">Valued Partner<br>Network</h2>
  <div class="badge" style="left:677px;top:617px" role="img" aria-label="Partner badge"></div>
  <div class="badge navy" style="left:777px;top:684px" role="img" aria-label="Partner badge"></div>
  <div class="badge" style="left:677px;top:752px" role="img" aria-label="Partner badge"></div>
  <div class="badge" style="left:777px;top:821px" role="img" aria-label="Partner badge"></div>
  <div class="badge blue" style="left:677px;top:887px" role="img" aria-label="Partner badge"></div>
  <div class="badge" style="left:777px;top:955px" role="img" aria-label="Partner badge"></div>

  <h2 class="abs heading" style="left:68px;top:822px">Services</h2>

  <div class="service" style="left:46px;top:886px">
    <div class="service-icon"><svg width="28" height="28" viewBox="0 0 28 28" fill="var(--navy)"><rect x="11" y="2" width="6" height="14" transform="rotate(-30 14 9)"/><rect x="3" y="23" width="22" height="3"/><path d="M7 23a9 9 0 0 1 12-11l-1 3a6 6 0 0 0-8 8z"/></svg></div>
    <div><h3>Regulatory Strategy</h3><p>•RAQA Organizational Structure<br>•Regulatory Pathway</p></div>
  </div>
  <div class="service" style="left:265px;top:886px">
    <div class="service-icon"><svg width="30" height="28" viewBox="0 0 30 28" fill="var(--navy)"><circle cx="8" cy="14" r="4"/><circle cx="22" cy="14" r="4"/><path d="M1 28c0-6 3-9 7-9s7 3 7 9zM15 28c0-6 3-9 7-9s7 3 7 9z"/><rect x="9" y="0" width="12" height="9" rx="2"/><path d="M12 4l2 2 4-4" stroke="#fff" stroke-width="1.5" fill="none"/></svg></div>
    <div><h3>FDA Communications</h3><p>•Deficiency Response<br>•Application Review</p></div>
  </div>
  <div class="service" style="left:46px;top:990px">
    <div class="service-icon"><svg width="26" height="28" viewBox="0 0 26 28" fill="var(--navy)"><path d="M5 2l4 4 4-5 4 5 4-4v6H5z"/><circle cx="13" cy="13" r="4"/><path d="M2 28c0-7 5-10 11-10s11 3 11 10z"/></svg></div>
    <div><h3>Interim Executive<br>Leadership</h3><p>•Compliance Remediation<br>•Accelerated Product Registration</p></div>
  </div>
  <div class="service" style="left:265px;top:995px">
    <div class="service-icon"><svg width="28" height="28" viewBox="0 0 28 28" fill="var(--navy)"><rect x="12" y="2" width="14" height="11" fill="none" stroke="var(--navy)" stroke-width="1.6"/><circle cx="6" cy="6" r="3"/><path d="M2 28V12h8l4-3 1 2-5 4v13z"/><circle cx="13" cy="18" r="2.4"/><circle cx="20" cy="18" r="2.4"/><path d="M10 28c0-4 1-6 3-6s3 2 3 6zM17 28c0-4 1-6 3-6s3 2 3 6z"/></svg></div>
    <div><h3>Training</h3><p>•FDA Communication<br>•MDR Reporting</p></div>
  </div>

  <div class="abs value">
    <h2>Harlow Ventures Value</h2>
    <div class="contact"><svg width="10" height="10" viewBox="0 0 10 10" fill="none" stroke="#222"><circle cx="5" cy="5" r="4.3"/><path d="M.7 5h8.6M5 .7c-2.4 2.6-2.4 6 0 8.6M5 .7c2.4 2.6 2.4 6 0 8.6"/></svg><a href="https://www.harlowventures.com">www.harlowventures.com</a></div>
    <div class="contact"><svg width="10" height="10" viewBox="0 0 10 10" fill="#222"><path d="M1 1.5l2-1 1.6 2.6-1.2 1c.6 1.2 1.4 2 2.5 2.5l1-1.2L9.5 7l-1 2C4.6 9 1 5.4 1 1.5z"/></svg>202.555.0147</div>
    <div class="contact"><svg width="10" height="10" viewBox="0 0 10 8" fill="#222"><path d="M0 0h10v8H0z"/><path d="M0 0l5 4 5-4" stroke="#fff" fill="none"/></svg><a href="mailto:info@harlowventures.com">info@harlowventures.com</a></div>
  </div>

</div>
</body>
</html>
```